Prayer Service 12.28.2013

I need a flyer designed for a Christian prayer service. The title and theme is:
"Total and Complete Surrender for Total and Complete Deliverance!"
1. You have creative freedom with imagery and typography
2. I need a quick turnaround time
FLYER DETAILS:
A prayer, anointing, and deliverance all night prayer service, at Valleybrook Assembly.
Saturday December 28 2013 from 9pm-6am.
Special guest speakers, prayer,anointing,and deliverance sessions.
For more information contact Sis Rosalind Okafor at Valleybrook Assembly 347 562 9140 Ext. 4816 or Marlene Cobb at 631 208-4392

```html
<!DOCTYPE html>
<html lang="en">
<head>
<meta charset="utf-8">
<title>Total Surrender for Complete Deliverance – All Night Prayer Service</title>
<link rel="stylesheet" href="https://fonts.googleapis.com/css2?family=PT+Sans+Narrow:wght@700&family=Arimo:wght@400&display=swap">
<style>
  :root {
    --backdrop: #2a1a12;
    --ink-black: #050403;
    --paper-light: #f6f1e6;
    --sepia-mid: #b8a88c;
    --sepia-deep: #6e5d46;
    --title-white: #ffffff;
    --deliverance-ink: #15110d;
    --body-white: #f4f4f4;
  }
  * { margin: 0; padding: 0; box-sizing: border-box; }
  html, body {
    width: 1157px;
    height: 1200px;
    overflow: hidden;
    background: var(--backdrop);
  }
  .flyer {
    position: absolute;
    left: 148px;
    top: 20px;
    width: 860px;
    height: 1160px;
    background: var(--ink-black);
    overflow: hidden;
  }
  .flyer__photo {
    position: absolute;
    inset: 0 0 auto 0;
    height: 860px;
    background:
      radial-gradient(ellipse 60% 45% at 18% 30%, var(--paper-light) 0%, rgba(246,241,230,0.6) 45%, rgba(246,241,230,0) 80%),
      radial-gradient(ellipse 40% 55% at 72% 60%, #a58e6d 0%, var(--sepia-deep) 55%, rgba(110,93,70,0) 100%),
      linear-gradient(160deg, #ece4d2 0%, var(--sepia-mid) 40%, var(--sepia-deep) 70%, var(--ink-black) 100%);
  }
  .flyer__photo::after {
    content: "";
    position: absolute;
    inset: 0;
    background: linear-gradient(180deg, rgba(5,4,3,0) 55%, rgba(5,4,3,0.85) 85%, var(--ink-black) 100%);
  }
  .flyer__title {
    position: absolute;
    right: 48px;
    top: 56px;
    text-align: right;
  }
  .flyer__title-lead {
    font-family: "PT Sans Narrow", "Arial Narrow", sans-serif;
    font-weight: 700;
    font-size: 82px;
    line-height: 0.92;
    color: var(--title-white);
    letter-spacing: 1px;
    text-shadow: 0 2px 6px rgba(0,0,0,0.35);
  }
  .flyer__title-main {
    font-family: "Arimo", Arial, sans-serif;
    font-weight: 400;
    font-size: 166px;
    line-height: 0.9;
    letter-spacing: -5px;
    color: var(--deliverance-ink);
    margin-top: -6px;
    margin-right: -6px;
  }
  .flyer__details {
    position: absolute;
    left: 58px;
    right: 48px;
    top: 800px;
    font-family: "Arimo", Arial, sans-serif;
    color: var(--body-white);
  }
  .flyer__para {
    font-size: 23px;
    line-height: 1.2;
    margin-bottom: 24px;
  }
  .flyer__contact {
    font-size: 23px;
    line-height: 1.2;
  }
  .flyer__contact-lines {
    font-size: 40px;
    line-height: 1.15;
    margin-top: 4px;
  }
</style>
</head>
<body>
  <main class="flyer">
    <div class="flyer__photo" role="img" aria-label="Photograph of folded praying hands resting on an open Bible in warm light"></div>

    <h1 class="flyer__title">
      <span class="flyer__title-lead">Total Surrender<br>for Complete</span><br>
      <span class="flyer__title-main">Deliverance</span>
    </h1>

    <section class="flyer__details">
      <p class="flyer__para">A prayer, anointing, and deliverance all night prayer service,<br>at Valleybrook Assembly.</p>
      <p class="flyer__para">Saturday December 28 2013 from 9pm-6am. Special guest speakers,<br>prayer,anointing, and deliverance sessions.</p>
      <p class="flyer__contact">For more information contact Sis Rosalind Okafor<br>at Valleybrook Assembly</p>
      <p class="flyer__contact-lines">347 562 9140 Ext. 4816 or<br>Marlene Cobb at 631 208-4392</p>
    </section>
  </main>
</body>
</html>
```